Irrigation Business needs their business cards modernised and revamped

I would like to keep my current logo, colours and revamp the format of the card.

I would like the card to be clean yet important.

Im not sure if you include texture but i would like the named logo to be indented into the card etc.

show me something alive and free something thats clinical to the point yet has a feel of achievement. i would like people to go nice card.

Target Market(s)

high end clients, corporate, sports field manger, the guys that make the decisions

Industry/Entity Type

Business

Contact Information for Business Card

nformation to be included

Dean Harlow (Director)
0487305526
dean@kolvat.biz
www.kestonfieldworks.com

instagram logo
google logo
facebook logo

Colors

Designer to choose colors to be used in the design.

Requirements
Nice to have
• indentations a really nice feel to the card good texture

```html
<!DOCTYPE html>
<html lang="en">
<head>
<meta charset="utf-8">
<title>Keston Irrigation Services – Business Card</title>
<link rel="stylesheet" href="https://fonts.googleapis.com/css2?family=Roboto:wght@400;700&family=Roboto+Condensed:wght@700&display=swap">
<style>
  :root {
    --backdrop: #262626;
    --paper: #f1f1f1;
    --brand-blue: #2f67a8;
    --sky-blue: #2fa3d4;
    --field-green: #2a9a55;
    --white: #ffffff;
  }
  * { margin: 0; padding: 0; box-sizing: border-box; }
  html, body { width: 1200px; height: 960px; overflow: hidden; }
  body {
    background: var(--backdrop);
    position: relative;
    font-family: "Roboto", Arial, sans-serif;
  }
  .card {
    position: absolute;
    width: 600px;
    height: 343px;
    background: var(--paper);
    overflow: hidden;
  }
  .card--front { left: 314px; top: 113px; }
  .card--back { left: 311px; top: 472px; }

  .wordmark {
    position: absolute;
    font-family: "Roboto Condensed", "Arial Narrow", sans-serif;
    font-weight: 700;
    color: var(--brand-blue);
    text-align: center;
    line-height: 1;
  }
  .wordmark__line { display: block; }
  .wordmark__sub { letter-spacing: 0.32em; }

  .card--front .wordmark { left: 38px; top: 60px; width: 228px; }
  .card--front .wordmark__main { font-size: 25px; letter-spacing: -0.01em; }
  .card--front .wordmark__sub { font-size: 16px; margin-top: 3px; }

  .person {
    position: absolute;
    right: 40px;
    top: 60px;
    text-align: right;
  }
  .person__name {
    font-family: "Roboto Condensed", "Arial Narrow", sans-serif;
    font-weight: 700;
    font-size: 22px;
    color: var(--brand-blue);
  }
  .person__role {
    font-size: 14px;
    font-weight: 400;
    color: var(--sky-blue);
    letter-spacing: 0.02em;
    margin-top: 3px;
  }

  .band {
    position: absolute;
    left: 0; top: 179px;
    width: 600px; height: 135px;
    background: var(--brand-blue);
  }
  .band__accent {
    position: absolute;
    right: 0; top: 0;
    width: 114px; height: 135px;
    background: var(--field-green);
  }
  .band__seal {
    position: absolute;
    left: 402px; top: -2px;
    width: 140px; height: 140px;
  }

  .contact {
    position: absolute;
    left: 40px; top: 22px;
    list-style: none;
    color: var(--white);
    font-size: 14.5px;
  }
  .contact__item {
    display: flex;
    align-items: center;
    height: 19px;
  }
  .contact__icon { width: 13px; height: 13px; margin-right: 8px; fill: var(--white); }

  .social {
    position: absolute;
    left: 39px; top: 89px;
    display: flex;
    gap: 3px;
  }
  .social__dot {
    width: 26px; height: 26px;
    border-radius: 50%;
    background: var(--white);
  }

  .back__seal {
    position: absolute;
    left: 246px; top: 80px;
    width: 106px; height: 106px;
    border-radius: 50%;
    background: var(--sky-blue);
    border: 4px solid var(--brand-blue);
  }
  .card--back .wordmark { left: 0; top: 196px; width: 600px; }
  .card--back .wordmark__main { font-size: 34px; }
  .card--back .wordmark__sub { font-size: 21px; margin-top: 4px; }
</style>
</head>
<body>

  <section class="card card--front" aria-label="Business card front">
    <h1 class="wordmark">
      <span class="wordmark__line wordmark__main">KESTON IRRIGATION</span>
      <span class="wordmark__line wordmark__sub">SERVICES</span>
    </h1>

    <div class="person">
      <p class="person__name">DEAN HARLOW</p>
      <p class="person__role">DIRECTOR</p>
    </div>

    <div class="band">
      <div class="band__accent"></div>

      <ul class="contact">
        <li class="contact__item">
          <svg class="contact__icon" viewBox="0 0 16 16" aria-hidden="true"><path d="M3.6 1.2l2.2 2.9-1.3 1.6c.9 2 2.7 3.8 4.8 4.8l1.6-1.3 2.9 2.2-1.2 2.6C7.4 14.3 1.7 8.6 1 2.4z"/></svg>
          0487305526
        </li>
        <li class="contact__item">
          <svg class="contact__icon" viewBox="0 0 16 16" aria-hidden="true"><path d="M1 3.5h14v1L8 9 1 4.5z M1 6l7 4.5L15 6v7H1z"/></svg>
          dean@kolvat.biz
        </li>
        <li class="contact__item">
          <svg class="contact__icon" viewBox="0 0 16 16" aria-hidden="true"><path d="M8 1a7 7 0 1 0 0 14A7 7 0 0 0 8 1zm-1 2.5l1.5 1-1 1.5-2 .5.5 2 2 .5 1 2-1 2.5C5 13 3 10.8 3 8c0-2 1.6-4 4-4.5zm3.5 1l2 1 .5 2.5-1.5-.5-1-1.5z"/></svg>
          www.kestonfieldworks.com
        </li>
      </ul>

      <div class="social" aria-label="Social profiles">
        <span class="social__dot"></span>
        <span class="social__dot"></span>
        <span class="social__dot"></span>
      </div>

      <svg class="band__seal" viewBox="0 0 140 140" aria-hidden="true">
        <circle cx="70" cy="70" r="68" fill="var(--white)"/>
        <circle cx="70" cy="70" r="64" fill="var(--brand-blue)"/>
        <circle cx="70" cy="70" r="61" fill="var(--sky-blue)"/>
      </svg>
    </div>
  </section>

  <section class="card card--back" aria-label="Business card back">
    <div class="back__seal" aria-hidden="true"></div>
    <h2 class="wordmark">
      <span class="wordmark__line wordmark__main">KESTON IRRIGATION</span>
      <span class="wordmark__line wordmark__sub">SERVICES</span>
    </h2>
  </section>

</body>
</html>
```